Need Web Design for Business Process Outsourcing Company (Quorvane)

Quorvane is a business process outsourcing company. Need a simple site similar to http://www.tallowbrinkhire.com/ but with a more professional and credible look. New to the process; not sure where to start and comparing my options. Please let me know what my options are if I choose to go with you. Logo is attached for your reference. Please use same colorway

Reason: I want the final product to be coded. Please confirm you will be able to code final design.

Industry/Entity Type

Business

Coding

Coded - Design and coding required

```html
<!DOCTYPE html>
<html lang="en">
<head>
<meta charset="utf-8">
<title>Quorvane Services</title>
<link href="https://fonts.googleapis.com/css2?family=Roboto:wght@400;500;700&family=Oswald:wght@500&display=swap" rel="stylesheet">
<style>
:root{
  --navy:#0b5388;
  --nav:#0c5a92;
  --bright:#1a8bd2;
  --deep:#08426c;
  --ink:#1c3f5e;
  --grey:#7a7a7a;
  --pale:#e3eef6;
  --field:#eeeeee;
  --white:#ffffff;
}
*{margin:0;padding:0;box-sizing:border-box}
html,body{width:1200px;height:3600px;overflow:hidden}
body{position:relative;font-family:"Roboto",Arial,sans-serif;color:var(--grey);background:var(--white)}
.abs{position:absolute}
p{font-size:15px;line-height:25px}

/* header */
.header{left:0;top:0;width:1200px;height:125px;background:var(--white)}
.brand{left:78px;top:22px;display:flex;align-items:center;gap:14px}
.brand-square{width:76px;height:76px;background:var(--navy);border-radius:8px}
.brand-name{font-size:46px;font-weight:700;color:var(--navy);letter-spacing:-1px}
.call{left:525px;top:62px;font-size:27px;color:#222}
.call span{color:var(--navy)}
.top-links{left:885px;top:14px;display:flex;gap:34px;font-size:17px;color:var(--bright)}
.top-links div{display:flex;align-items:center;gap:8px}
.search{left:820px;top:60px;width:305px;height:48px;border:1px solid #bbb;display:flex;align-items:center;justify-content:space-between;padding:0 12px;font-size:14px;color:#555}

/* nav */
.nav{left:0;top:125px;width:1200px;height:65px;background:var(--nav);display:flex;padding-left:77px}
.nav a{color:var(--white);text-decoration:none;font-size:16px;font-weight:500;line-height:65px;padding:0 27px}
.nav a.active{background:var(--bright)}

/* hero */
.hero-photo{left:0;top:190px;width:1200px;height:460px;background:linear-gradient(135deg,#dfe9f1 0%,#b9cad8 35%,#7f97ad 65%,#c8d6e2 100%)}
.hero-box{left:190px;top:305px;width:800px;height:210px;background:rgba(20,40,60,.72);text-align:center;color:var(--white);padding-top:20px}
.hero-title{font-family:"Oswald","Arial Narrow",sans-serif;font-size:66px;line-height:72px;font-weight:500}
.hero-box p{font-size:15px;line-height:22px;padding:4px 30px 0}
.btn{display:inline-block;background:var(--bright);color:var(--white);font-size:20px;font-weight:500;padding:0 24px;line-height:56px;text-transform:uppercase}
.hero-box .btn{margin-top:14px}
.hero-curve{left:0;top:480px}

/* welcome */
.welcome{left:0;top:640px;width:1200px;height:360px;background:var(--navy)}
.badge{left:552px;top:660px;width:96px;height:96px;border-radius:50%;background:var(--white)}
.welcome-title{left:0;top:785px;width:1200px;text-align:center;color:var(--white);font-size:45px;font-weight:500}
.welcome-text{left:120px;top:843px;width:960px;text-align:center;color:#dbe7f1;font-size:14px;line-height:24px}

/* services */
.services{left:55px;top:948px;width:1090px;display:flex;justify-content:space-between}
.service{width:210px;text-align:center}
.service-icon{width:114px;height:114px;margin:0 auto;border-radius:50%;background:var(--navy);border:4px solid var(--white);box-shadow:0 0 0 3px var(--navy);display:flex;align-items:center;justify-content:center}
.service-icon.on{background:var(--bright);box-shadow:0 0 0 3px var(--bright)}
.service h3{margin-top:24px;font-size:21px;font-weight:500;color:var(--navy)}
.service.on h3{color:var(--bright)}
.service p{font-size:14px;line-height:25px;margin-top:6px}
.service .chev{margin-top:14px}

/* features */
.features{left:0;top:1284px;width:1200px;height:372px;background:linear-gradient(90deg,#e8f1f8 0%,#d6e6f2 50%,#eef5fa 100%)}
.feat{width:300px}
.feat h3{font-size:21px;font-weight:500;color:var(--navy)}
.feat p{font-size:14px;line-height:25px;margin-top:4px}
.feat.left{text-align:right}
.feat-icon{width:102px;height:102px;background:var(--navy);border-radius:8px;display:flex;align-items:center;justify-content:center}

/* news */
.section-title{width:1200px;left:0;text-align:center;color:var(--ink);font-size:42px;font-weight:500}
.news-photo{width:208px;height:160px}
.news h3{font-size:20px;font-weight:500;color:var(--navy)}
.news .date{font-size:15px;color:var(--navy);margin:10px 0 6px;display:flex;gap:8px;align-items:center}
.news p{font-size:14px;line-height:25px}
.news .more{font-size:13px;font-weight:700;color:var(--navy);margin-top:4px}

/* global */
.global{left:0;top:2000px;width:1200px;height:365px;background:linear-gradient(180deg,#cfe2ef 0%,#e4eff7 100%)}
.map{left:80px;top:2040px;width:410px;height:280px;border-radius:50%;background:radial-gradient(ellipse at center,#f2f2f2 0%,#cfcfcf 70%,#b9c3cc 100%)}
.global-title{left:542px;top:2050px;font-size:44px;font-weight:500;color:var(--navy)}
.global-text{left:542px;top:2115px;width:580px;font-size:15px;line-height:25px;color:#8a9aa8}

/* passion */
.passion{left:0;top:2365px;width:1200px;height:395px;background:linear-gradient(180deg,#e6f0f7 0%,#ffffff 100%)}
.passion-art{left:625px;top:2375px;width:575px;height:385px;background:linear-gradient(135deg,rgba(255,255,255,0) 0%,#c9d6e3 40%,#b7a58f 80%,#d9d9d9 100%)}
.passion-title{left:80px;top:2402px;width:850px;font-size:38px;line-height:48px;font-weight:500;color:var(--navy)}
.passion-text{left:80px;top:2500px;width:800px;font-size:14px;line-height:25px;color:#555}

/* contact */
.contact-text{left:150px;top:2895px;width:900px;text-align:center;font-size:14px;line-height:25px}
.field{background:var(--field);border:1px solid #dadada;font-size:14px;color:#555;padding:18px 14px}

/* footer */
.footer{left:0;top:3257px;width:1200px;height:276px;background:var(--navy);color:var(--white)}
.foot-brand{left:80px;top:3285px;display:flex;align-items:center;gap:12px}
.foot-brand .brand-square{width:54px;height:54px;background:var(--white)}
.foot-brand .brand-name{color:var(--white);font-size:36px}
.foot-text{font-size:14px;line-height:27px;color:#e3edf5}
.foot-head{font-size:19px;font-weight:500;letter-spacing:.5px}
.social{left:80px;top:3450px;display:flex;gap:14px}
.social span{width:44px;height:44px;border-radius:50%;border:2px solid var(--bright)}
.social span:first-child{background:var(--bright)}
.links{list-style:none;font-size:14px;line-height:24px;color:#e3edf5}
.links li{display:flex;align-items:center;gap:12px}
.links li::before{content:"";width:9px;height:9px;border:1px solid #9fc2dd}
.links li:first-child::before{background:var(--bright);border-color:var(--bright)}
.contact-row{display:flex;gap:16px;align-items:flex-start;font-size:14px;line-height:26px;color:#e3edf5}
.news-input{background:var(--white);color:#333;font-size:14px;padding:0 10px;line-height:44px;width:250px}
.copy{left:0;top:3533px;width:1200px;height:67px;background:var(--bright);color:var(--white);text-align:center;line-height:67px;font-size:15px}
</style>
</head>
<body>

<header class="header abs">
  <div class="brand abs"><span class="brand-square"></span><span class="brand-name">Quorvane</span></div>
  <div class="top-links abs">
    <div><svg width="24" height="20" viewBox="0 0 24 20"><path d="M2 2h20v12H9l-5 4v-4H2z" fill="none" stroke="#1a8bd2" stroke-width="2"/></svg>Live Chat</div>
    <div><svg width="26" height="18" viewBox="0 0 26 18"><rect x="1" y="1" width="24" height="16" fill="none" stroke="#0b5388" stroke-width="2"/><path d="M1 1l12 9 12-9" fill="none" stroke="#0b5388" stroke-width="2"/></svg>Email Us</div>
  </div>
  <div class="call abs">Call Us On : <span>123 456 7890</span></div>
  <div class="search abs">Search...<svg width="20" height="20" viewBox="0 0 20 20"><circle cx="8" cy="8" r="6" fill="none" stroke="#0b5388" stroke-width="3"/><path d="M12.5 12.5l6 6" stroke="#0b5388" stroke-width="3"/></svg></div>
</header>

<nav class="nav abs">
  <a class="active">HOME</a><a>ABOUT</a><a>OUR SERVICES</a><a>OUR STRATEGY</a><a>OUR EXPERIENCY</a><a>SECURITY</a><a>NEWS</a><a>CONTACT</a>
</nav>

<div class="hero-photo abs" role="img" aria-label="Photo of a support team working at computers in a bright office"></div>
<div class="welcome abs"></div>
<svg class="hero-curve abs" width="1200" height="170" viewBox="0 0 1200 170">
  <path d="M0 40 Q600 250 1200 40 L1200 170 L0 170Z" fill="#0b5388"/>
  <path d="M0 40 Q600 250 1200 40" fill="none" stroke="#ffffff" stroke-width="6"/>
</svg>
<div class="hero-box abs">
  <div class="hero-title">QUORVANE SERVICES</div>
  <p>Lorem Ipsum is simply dummy text of the printing and typesetting industry. Lorem Ipsum has been the industry's standard dummy text ever since the 1500s, when an unknown</p>
  <span class="btn">Contact us know</span>
</div>

<div class="badge abs"></div>
<h2 class="welcome-title abs">WELCOME TO QUORVANE SERVICES</h2>
<p class="welcome-text abs">Lorem Ipsum is simply dummy text of the printing and typesetting industry. Lorem Ipsum has been the industry's standard dummy text ever since the 1500s, when an unknown printer took a galley of type and scrambled it to make a type specimen book. It has survived not only five centuries, but also the leap into electronic typesetting, remaining essentially unchanged.</p>

<div class="services abs">
  <div class="service">
    <div class="service-icon"><svg width="60" height="60" viewBox="0 0 60 60" fill="none" stroke="#fff" stroke-width="4"><path d="M10 32a20 20 0 0 1 40 0"/><rect x="6" y="30" width="10" height="16" rx="3" fill="#fff"/><rect x="44" y="30" width="10" height="16" rx="3" fill="#fff"/><path d="M49 46q0 8-14 8"/></svg></div>
    <h3>CUSTOMER SERVICE</h3><p>Lorem Ipsum is simply text of dummy text of the printing and type setting..</p>
    <svg class="chev" width="22" height="20" viewBox="0 0 22 20" fill="none" stroke="#1a8bd2" stroke-width="3"><path d="M3 2l8 7 8-7M3 10l8 7 8-7"/></svg>
  </div>
  <div class="service">
    <div class="service-icon"><svg width="60" height="60" viewBox="0 0 60 60" fill="none" stroke="#fff" stroke-width="4"><path d="M6 12h8l6 26h26l6-18H17"/><circle cx="23" cy="47" r="4" fill="#fff"/><circle cx="43" cy="47" r="4" fill="#fff"/></svg></div>
    <h3>ECOMMERCE</h3><p>Lorem Ipsum is simply text of dummy text of the printing and type setting..</p>
    <svg class="chev" width="22" height="20" viewBox="0 0 22 20" fill="none" stroke="#1a8bd2" stroke-width="3"><path d="M3 2l8 7 8-7M3 10l8 7 8-7"/></svg>
  </div>
  <div class="service on">
    <div class="service-icon on"><svg width="60" height="60" viewBox="0 0 60 60" fill="none" stroke="#fff" stroke-width="4"><rect x="8" y="8" width="44" height="32"/><path d="M30 40v10M18 52h24M20 16l20 16M40 16L20 32"/></svg></div>
    <h3>CREATIVE</h3><p>Lorem Ipsum is simply text of dummy text of the printing and type setting..</p>
    <svg class="chev" width="22" height="20" viewBox="0 0 22 20" fill="none" stroke="#1a8bd2" stroke-width="3"><path d="M3 2l8 7 8-7M3 10l8 7 8-7"/></svg>
  </div>
  <div class="service">
    <div class="service-icon"><svg width="60" height="60" viewBox="0 0 60 60" fill="none" stroke="#fff" stroke-width="4"><path d="M22 40a14 14 0 1 1 16 0v6H22z"/><path d="M24 52h12M30 4v4M10 12l3 3M50 12l-3 3M6 28h4M50 28h4"/></svg></div>
    <h3>IT SOLUTIONS</h3><p>Lorem Ipsum is simply text of dummy text of the printing and type setting..</p>
    <svg class="chev" width="22" height="20" viewBox="0 0 22 20" fill="none" stroke="#1a8bd2" stroke-width="3"><path d="M3 2l8 7 8-7M3 10l8 7 8-7"/></svg>
  </div>
  <div class="service">
    <div class="service-icon"><svg width="60" height="60" viewBox="0 0 60 60" fill="#fff"><circle cx="30" cy="18" r="8"/><circle cx="14" cy="24" r="6"/><circle cx="46" cy="24" r="6"/><path d="M18 46a12 12 0 0 1 24 0z"/><path d="M4 46a10 10 0 0 1 16-8v8zM56 46a10 10 0 0 0-16-8v8z"/></svg></div>
    <h3>HUMAN RESOURCES</h3><p>Lorem Ipsum is simply text of dummy text of the printing and type setting..</p>
    <svg class="chev" width="22" height="20" viewBox="0 0 22 20" fill="none" stroke="#1a8bd2" stroke-width="3"><path d="M3 2l8 7 8-7M3 10l8 7 8-7"/></svg>
  </div>
</div>

<section class="features abs"></section>
<div class="feat left abs" style="left:160px;top:1345px"><h3>REINVENTING SERVICES</h3><p>Lorem Ipsum is simply dummy text of the printing and typesetting industry. Lorem Ipsum has been the.</p></div>
<div class="feat left abs" style="left:160px;top:1478px"><h3>OUR PEOPLE</h3><p>Lorem Ipsum is simply dummy text of the printing and typesetting industry. Lorem Ipsum has been the.</p></div>
<div class="feat abs" style="left:738px;top:1345px"><h3>OUR FACILITES</h3><p>Lorem Ipsum is simply dummy text of the printing and typesetting industry. Lorem Ipsum has been the.</p></div>
<div class="feat abs" style="left:738px;top:1478px"><h3>SUCCESS STOIES</h3><p>Lorem Ipsum is simply dummy text of the printing and typesetting industry. Lorem Ipsum has been the.</p></div>
<div class="feat-icon abs" style="left:480px;top:1345px"><svg width="62" height="62" viewBox="0 0 62 62" fill="none" stroke="#fff" stroke-width="5"><circle cx="22" cy="24" r="10"/><circle cx="44" cy="44" r="7"/><path d="M22 6v6M22 36v6M4 24h6M34 24h6M44 32v4M44 52v4M32 44h4M52 44h4"/></svg></div>
<div class="feat-icon abs" style="left:618px;top:1345px"><svg width="62" height="62" viewBox="0 0 62 62" fill="#fff"><rect x="8" y="24" width="18" height="32"/><rect x="30" y="8" width="24" height="48"/><g fill="#0b5388"><rect x="35" y="14" width="5" height="5"/><rect x="44" y="14" width="5" height="5"/><rect x="35" y="26" width="5" height="5"/><rect x="44" y="26" width="5" height="5"/><rect x="35" y="38" width="5" height="5"/><rect x="44" y="38" width="5" height="5"/><rect x="13" y="30" width="8" height="4"/><rect x="13" y="40" width="8" height="4"/></g></svg></div>
<div class="feat-icon abs" style="left:480px;top:1480px"><svg width="62" height="62" viewBox="0 0 62 62" fill="none" stroke="#fff" stroke-width="5"><path d="M6 48l16-16 10 10 22-22M40 18h16v16"/></svg></div>
<div class="feat-icon abs" style="left:618px;top:1480px"><svg width="62" height="62" viewBox="0 0 62 62" fill="#fff"><circle cx="31" cy="18" r="9"/><circle cx="13" cy="26" r="6"/><circle cx="49" cy="26" r="6"/><path d="M17 52a14 14 0 0 1 28 0z"/><path d="M2 50a11 11 0 0 1 18-8v8zM60 50a11 11 0 0 0-18-8v8z"/></svg></div>

<h2 class="section-title abs" style="top:1702px">LATEST NEWS</h2>
<div class="news-photo abs" style="left:80px;top:1780px;background:linear-gradient(135deg,#e7dccb,#6d7c8f 60%,#2e3a4a)" role="img" aria-label="Photo of two businesspeople reviewing documents"></div>
<div class="news abs" style="left:305px;top:1778px;width:300px"><h3>LOREM IPSUM IS SIMPLE TEXT</h3><div class="date"><svg width="16" height="16" viewBox="0 0 16 16"><rect x="1" y="3" width="14" height="12" fill="none" stroke="#0b5388" stroke-width="2"/><path d="M1 7h14M5 1v4M11 1v4" stroke="#0b5388" stroke-width="2"/></svg>11 Nov 2016</div><p>Lorem Ipsum is simply dummy text of the printing and typesetting Lorem Ipsum has been the industry's standard dummy text</p><div class="more">READ MORE... &raquo;</div></div>
<div class="news-photo abs" style="left:610px;top:1780px;background:linear-gradient(135deg,#f4f4f4,#9aa7b4 55%,#3d4b5c)" role="img" aria-label="Photo of a business handshake"></div>
<div class="news abs" style="left:833px;top:1778px;width:300px"><h3>LOREM IPSUM IS SIMPLE TEXT</h3><div class="date"><svg width="16" height="16" viewBox="0 0 16 16"><rect x="1" y="3" width="14" height="12" fill="none" stroke="#0b5388" stroke-width="2"/><path d="M1 7h14M5 1v4M11 1v4" stroke="#0b5388" stroke-width="2"/></svg>11 Nov 2016</div><p>Lorem Ipsum is simply dummy text of the printing and typesetting Lorem Ipsum has been the industry's standard dummy text</p><div class="more">READ MORE... &raquo;</div></div>

<section class="global abs"></section>
<div class="map abs" role="img" aria-label="World map with office locations"></div>
<h2 class="global-title abs">GLOBAL PRESENCE</h2>
<p class="global-text abs">Lorem Ipsum is simply dummy text of the printing and typesetting industry. Lorem Ipsum has been the industry's standard dummy text ever since the 1500s, when an unknown printer took a galley of type and scrambled it to make a type specimen book. It has survived not only five centuries, but also the leap into electronic typesetting, remaining essentially unchanged.</p>
<span class="btn abs" style="left:542px;top:2256px;font-size:19px;line-height:54px">Know more</span>

<section class="passion abs"></section>
<div class="passion-art abs" role="img" aria-label="Illustration of hands holding colourful links forming an upward arrow"></div>
<h2 class="passion-title abs">PASSIONATE ABOUT ENGAGING WITH CLIENTS &amp; GROWING BUSINESS ?</h2>
<p class="passion-text abs">Lorem Ipsum is simply dummy text of the printing and typesetting industry. Lorem Ipsum has been the industry's standard dummy text ever since the 1500s, when an unknown printer took a galley of type and scrambled it to make a type specimen book. It has survived not only five centuries, but also the leap into electronic typesetting, remaining essentially unchanged. Lorem Ipsum is simply dummy text of the printing and typesetting industry. Lorem Ipsum has been the industry's standard dummy text ever since the 1500s, when an</p>
<span class="btn abs" style="left:80px;top:2652px;font-size:19px;line-height:54px;padding:0 16px">Apply know</span>

<h2 class="section-title abs" style="top:2815px">CONTACT US</h2>
<p class="contact-text abs">Lorem Ipsum is simply dummy text of the printing and typesetting industry. Lorem Ipsum has been the industry's standard dummy text ever since the 1500s, when an unknown printer took a galley of type and scrambled it to</p>
<div class="field abs" style="left:168px;top:2952px;width:281px;height:53px">Name*</div>
<div class="field abs" style="left:461px;top:2952px;width:278px;height:53px">Email*</div>
<div class="field abs" style="left:751px;top:2952px;width:281px;height:53px">Phone*</div>
<div class="field abs" style="left:168px;top:3014px;width:864px;height:111px">Message*</div>
<span class="btn abs" style="left:516px;top:3137px;width:168px;text-align:center;line-height:55px">Submit</span>

<footer class="footer abs"></footer>
<div class="foot-brand abs"><span class="brand-square"></span><span class="brand-name">Quorvane</span></div>
<p class="foot-text abs" style="left:80px;top:3370px;width:250px">Lorem Ipsum is simply dummy text of the print ing and typesetting industry. Lorem Ipsum has been the.</p>
<div class="social abs"><span></span><span></span><span></span></div>

<div class="foot-head abs" style="left:345px;top:3285px">USEFULL LINKS</div>
<ul class="links abs" style="left:345px;top:3322px"><li>Home</li><li>About</li><li>Services</li><li>Strategy</li><li>Experiency</li><li>Security</li><li>News</li><li>Contact</li></ul>

<div class="foot-head abs" style="left:608px;top:3285px">GET IN TOUCH</div>
<div class="contact-row abs" style="left:608px;top:3322px;width:240px"><svg width="22" height="18" viewBox="0 0 22 18"><rect x="1" y="1" width="20" height="16" fill="none" stroke="#9fc2dd" stroke-width="2"/><path d="M5 6h12M5 11h8" stroke="#9fc2dd" stroke-width="2"/></svg><span>101- Lorem ipsum is simple dummy text of print and type setting industry</span></div>
<div class="contact-row abs" style="left:608px;top:3410px"><svg width="22" height="22" viewBox="0 0 22 22"><path d="M4 2l5 1 1 5-3 2q2 5 5 6l2-3 5 1 1 5q-2 3-6 2Q5 19 2 8 1 4 4 2z" fill="#9fc2dd"/></svg><span>123 456 7890</span></div>
<div class="contact-row abs" style="left:608px;top:3455px"><svg width="22" height="16" viewBox="0 0 22 16"><rect x="1" y="1" width="20" height="14" fill="none" stroke="#9fc2dd" stroke-width="2"/><path d="M1 1l10 8 10-8" fill="none" stroke="#9fc2dd" stroke-width="2"/></svg><span>info@quorvaneservices.com</span></div>

<div class="foot-head abs" style="left:873px;top:3285px">NEWSLETTER</div>
<p class="foot-text abs" style="left:873px;top:3318px;width:260px;line-height:24px">Would you like to receive exclusive access to articles, white papers and our regular monthly newsletter?</p>
<div class="news-input abs" style="left:873px;top:3396px">Enter Email Id</div>
<span class="btn abs" style="left:873px;top:3450px;width:155px;text-align:center;font-size:18px;line-height:42px;padding:0">Submit</span>

<div class="copy abs">&copy; QUORVANE SERVICES - 2016 All rights reserved.</div>

</body>
</html>
```